Marlow Vale Stud website

We would like to create a horse stud/agistment farm website similar to this websites we have attached below:
www.thornbeck.com.au
www.quillstead.com.au
www.brackley.com
www.pimsey.com.au
The main colour scheme are purple and white to align with the stable's racing colours.
We have also attach the company logo and also images of the farm and create some ideas for the website.
Many thanks for looking into this project!

```html
<!DOCTYPE html>
<html lang="en">
<head>
<meta charset="utf-8">
<title>Marlow Vale Stud</title>
<link href="https://fonts.googleapis.com/css2?family=Cinzel:wght@700&family=Montserrat:wght@400;600;700&family=Open+Sans:ital,wght@0,400;0,600;1,400&family=Lora:wght@700&display=swap" rel="stylesheet">
<style>
:root{
  --purple:#4b1b50;
  --purple-deep:#3a1240;
  --white:#ffffff;
  --paper:#f1f0ee;
  --ink:#2b2b2b;
  --muted:#8a8a8a;
  --footer:#2a231f;
  --footer-text:#b9b1aa;
  --grass:#4d7a2a;
}
*{margin:0;padding:0;box-sizing:border-box}
html,body{width:1200px;height:2716px;overflow:hidden;background:var(--white)}
body{font-family:'Open Sans',sans-serif;color:var(--ink);position:relative}
.page{position:relative;width:1200px;height:2716px;overflow:hidden}

/* header */
.site-header{position:absolute;top:0;left:0;width:1200px;height:112px;background:var(--purple)}
.brand{position:absolute;left:70px;top:28px;display:flex;align-items:center;gap:12px;color:var(--white);font-family:'Montserrat',sans-serif;font-weight:700;font-size:22px}
.brand-dot{width:44px;height:44px;border-radius:50%;border:3px solid var(--white)}
.phone{position:absolute;right:88px;top:12px;color:var(--white);font-family:'Montserrat',sans-serif;font-size:17px;display:flex;align-items:center;gap:10px}
.main-nav{position:absolute;right:70px;top:64px;display:flex;gap:30px;font-family:'Montserrat',sans-serif;font-size:13px;font-weight:600;letter-spacing:.5px}
.main-nav a{color:#d9c9dc;text-decoration:none}
.main-nav a.active{color:var(--white)}

/* hero */
.hero{position:absolute;top:112px;left:0;width:1200px;height:560px;background:linear-gradient(180deg,#a9b2b4 0%,#8d9698 30%,#5f6b45 46%,#4f7a2f 60%,#3f6a24 100%)}
.hero-title{position:absolute;top:70px;width:1200px;text-align:center;color:var(--white);font-family:'Montserrat',sans-serif;font-weight:700;font-size:54px}
.hero-sub{position:absolute;top:152px;width:1200px;text-align:center;color:var(--white);font-family:'Montserrat',sans-serif;font-size:20px}
.slider-dots{position:absolute;left:1056px;top:522px;display:flex;gap:8px}
.slider-dots span{width:14px;height:14px;border-radius:50%;border:2px solid var(--white)}
.slider-dots span.on{background:var(--white)}

/* sections */
.section-title{position:absolute;width:1200px;text-align:center;color:var(--purple);font-family:'Cinzel',serif;font-weight:700;font-size:42px;letter-spacing:1px}
.stallions{position:absolute;top:672px;left:0;width:1200px;height:528px;background:var(--paper)}
.stallion-card{position:absolute;top:160px;width:316px;height:288px}
.stallion-photo{width:100%;height:232px}
.stallion-name{height:56px;background:var(--purple);color:var(--white);font-family:'Montserrat',sans-serif;font-size:17px;text-align:center;line-height:56px}

.about{position:absolute;top:1200px;left:0;width:1200px;height:520px;background:var(--white)}
.about-photo-a{position:absolute;left:76px;top:60px;width:256px;height:356px;background:linear-gradient(180deg,#9aa0a2 0%,#6f7566 45%,#4b6b2d 100%)}
.about-photo-b{position:absolute;left:344px;top:104px;width:256px;height:360px;background:linear-gradient(180deg,#3c3a3c 0%,#7a6a70 40%,#6b8a3f 80%,#4f7a2f 100%)}
.about-title{position:absolute;left:688px;top:124px;font-family:'Cinzel',serif;font-weight:700;font-size:40px;color:var(--purple)}
.about-lead{position:absolute;left:688px;top:178px;font-style:italic;font-size:17px;color:var(--purple)}
.about-text{position:absolute;left:688px;top:214px;width:420px;font-size:13px;line-height:22px;color:var(--muted)}
.btn{display:inline-block;background:var(--purple);color:var(--white);font-family:'Montserrat',sans-serif;font-weight:700;font-size:14px;letter-spacing:1px;text-align:center;text-decoration:none}
.about .btn{position:absolute;left:688px;top:360px;width:168px;height:52px;line-height:52px}

.news{position:absolute;top:1720px;left:0;width:1200px;height:600px;background:var(--paper)}
.news-card{position:absolute;top:152px;width:248px}
.news-photo{position:relative;width:248px;height:184px}
.news-date{position:absolute;left:0;top:0;width:64px;height:72px;background:var(--purple);color:var(--white);text-align:center;font-family:'Montserrat',sans-serif}
.news-date b{display:block;font-size:26px;line-height:34px;padding-top:8px}
.news-date small{font-size:12px}
.news-title{margin-top:16px;font-family:'Lora',serif;font-weight:700;font-size:15px;line-height:22px;color:var(--ink)}
.news-text{margin-top:10px;font-size:12px;line-height:20px;color:var(--muted)}

/* footer */
.grass{position:absolute;top:2290px;left:0;width:1200px;height:56px;background:linear-gradient(180deg,#6d9a3a 0%,var(--grass) 50%,#2e3a1c 100%)}
.site-footer{position:absolute;top:2340px;left:0;width:1200px;height:376px;background:var(--footer);color:var(--footer-text)}
.footer-brand{position:absolute;left:76px;top:40px;display:flex;align-items:center;gap:12px;color:var(--white);font-family:'Montserrat',sans-serif;font-weight:700;font-size:20px}
.footer-about{position:absolute;left:76px;top:110px;width:300px;font-size:12px;line-height:20px}
.socials{position:absolute;left:76px;top:200px;display:flex;gap:12px}
.socials span{width:36px;height:36px;border-radius:50%;background:#2f7fd1}
.socials span:nth-child(2){background:#2aa9e0}
.socials span:nth-child(3){background:#5a6ea8}
.footer-col{position:absolute;top:40px}
.footer-col h4{font-family:'Montserrat',sans-serif;font-weight:700;font-size:15px;letter-spacing:1px;color:var(--white);margin-bottom:26px}
.contact-row{display:flex;gap:14px;font-size:13px;line-height:20px;margin-bottom:22px;width:280px}
.contact-row svg{flex:none;margin-top:2px}
.newsletter p{font-size:12px;line-height:20px;width:300px}
.email-field{margin-top:28px;width:200px;height:36px;background:var(--white);color:#999;font-size:12px;line-height:36px;padding-left:12px}
.newsletter .btn{margin-top:16px;width:160px;height:42px;line-height:42px}
.copyright{position:absolute;top:332px;width:1200px;text-align:center;font-size:11px}
</style>
</head>
<body>
<div class="page">

<header class="site-header">
  <div class="brand"><span class="brand-dot"></span>Marlow Vale Stud</div>
  <div class="phone">
    <svg width="18" height="18" viewBox="0 0 24 24"><path fill="#fff" d="M6.6 10.8a15.1 15.1 0 0 0 6.6 6.6l2.2-2.2a1 1 0 0 1 1-.25 11.4 11.4 0 0 0 3.6.57 1 1 0 0 1 1 1V20a1 1 0 0 1-1 1A17 17 0 0 1 3 4a1 1 0 0 1 1-1h3.5a1 1 0 0 1 1 1c0 1.25.2 2.45.57 3.57a1 1 0 0 1-.25 1z"/></svg>
    123 456 7890
  </div>
  <nav class="main-nav">
    <a class="active" href="#">HOME ▾</a><a href="#">STALLIONS</a><a href="#">NEWS</a><a href="#">SALES</a><a href="#">GALLERY</a><a href="#">ABOUT</a><a href="#">CONTACT</a>
  </nav>
</header>

<section class="hero" role="img" aria-label="Pale horse standing on a green paddock under a cloudy sky">
  <h1 class="hero-title">Our kingdom For A Horse</h1>
  <p class="hero-sub">Inter Relation Between Horse &amp; Rider</p>
  <div class="slider-dots"><span class="on"></span><span></span><span></span><span></span><span></span></div>
</section>

<section class="stallions">
  <h2 class="section-title" style="top:56px">STALLIONS</h2>
  <div class="stallion-card" style="left:-88px">
    <div class="stallion-photo" role="img" aria-label="Two bay horses running in a field" style="background:linear-gradient(180deg,#c9c6bd,#8a5a3a 60%,#6f8a4a)"></div>
    <div class="stallion-name" style="padding-left:88px">Bramble</div>
  </div>
  <div class="stallion-card" style="left:264px">
    <div class="stallion-photo" role="img" aria-label="Dark bay stallion portrait" style="background:linear-gradient(180deg,#6b4a35,#3c2418 70%,#5a3a28)"></div>
    <div class="stallion-name">Stillbrook</div>
  </div>
  <div class="stallion-card" style="left:620px">
    <div class="stallion-photo" role="img" aria-label="Chestnut stallion head portrait" style="background:linear-gradient(180deg,#d8cdb8,#b0622e 55%,#7a3f1c)"></div>
    <div class="stallion-name">Harbour King</div>
  </div>
  <div class="stallion-card" style="left:968px">
    <div class="stallion-photo" role="img" aria-label="Grey horses galloping on grass" style="background:linear-gradient(180deg,#9aa4a6,#c9c9c4 45%,#5c7a3a)"></div>
    <div class="stallion-name" style="padding-right:84px">Ever So Swift</div>
  </div>
</section>

<section class="about">
  <div class="about-photo-a" role="img" aria-label="Horse and rider in a paddock under a stormy sky"></div>
  <div class="about-photo-b" role="img" aria-label="Jockey in silks riding a grey racehorse"></div>
  <h2 class="about-title">ABOUT</h2>
  <p class="about-lead">We've made a life that will change you</p>
  <p class="about-text">Lorem ipsum is simply dummy text of the printing and typesetting industry. Lorem ipsum has been the industry's standard dummy text ever since the 1500s, when an unknown printer took a galley of type and scrambled it to make a type specimen book.</p>
  <a class="btn" href="#">LEARN MORE</a>
</section>

<section class="news">
  <h2 class="section-title" style="top:44px">LATEST NEWS</h2>
  <article class="news-card" style="left:76px">
    <div class="news-photo" role="img" aria-label="Rider on horseback under a blue sky" style="background:linear-gradient(180deg,#3f7fc8,#8fb6dc 55%,#9a8a6a)"><div class="news-date"><b>07</b><small>MAY</small></div></div>
    <h3 class="news-title">Lorem Ipsum is simply text of the printing &amp; type.</h3>
    <p class="news-text">Lorem ipsum is simply dummy text of the printing and typesetting industry. Lorem ipsum has been the industry's standard.</p>
  </article>
  <article class="news-card" style="left:344px">
    <div class="news-photo" role="img" aria-label="Tree lined country track" style="background:linear-gradient(180deg,#cfd9c0,#6f8a45 50%,#a68a5a)"><div class="news-date"><b>07</b><small>MAY</small></div></div>
    <h3 class="news-title">Lorem Ipsum is simply text of the printing &amp; type.</h3>
    <p class="news-text">Lorem ipsum is simply dummy text of the printing and typesetting industry. Lorem ipsum has been the industry's standard.</p>
  </article>
  <article class="news-card" style="left:612px">
    <div class="news-photo" role="img" aria-label="Group of horses standing in a field" style="background:linear-gradient(180deg,#4a86cf,#9cc0e2 45%,#4d6a2e)"><div class="news-date"><b>07</b><small>MAY</small></div></div>
    <h3 class="news-title">Lorem Ipsum is simply text of the printing &amp; type.</h3>
    <p class="news-text">Lorem ipsum is simply dummy text of the printing and typesetting industry. Lorem ipsum has been the industry's standard.</p>
  </article>
  <article class="news-card" style="left:880px">
    <div class="news-photo" role="img" aria-label="Aerial view of green farm paddocks" style="background:linear-gradient(180deg,#6aa0c8,#5f9a3a 40%,#3f7a28)"><div class="news-date"><b>07</b><small>MAY</small></div></div>
    <h3 class="news-title">Lorem Ipsum is simply text of the printing &amp; type.</h3>
    <p class="news-text">Lorem ipsum is simply dummy text of the printing and typesetting industry. Lorem ipsum has been the industry's standard.</p>
  </article>
</section>

<div class="grass" role="img" aria-label="Strip of grass along the top of the footer"></div>

<footer class="site-footer">
  <div class="footer-brand"><span class="brand-dot"></span>Marlow Vale Stud</div>
  <p class="footer-about">Lorem ipsum is simply dummy text of the printing and typesetting industry. Lorem ipsum has been the industry's standard.</p>
  <div class="socials"><span></span><span></span><span></span></div>

  <div class="footer-col" style="left:440px">
    <h4>CONTACT US</h4>
    <div class="contact-row">
      <svg width="14" height="18" viewBox="0 0 14 18"><path fill="#fff" d="M7 0a7 7 0 0 0-7 7c0 5 7 11 7 11s7-6 7-11a7 7 0 0 0-7-7zm0 9.5A2.5 2.5 0 1 1 7 4.5a2.5 2.5 0 0 1 0 5z"/></svg>
      <span>Marlow Vale Stud<br>102 Green Hill Road, Marlow Vale NSW 2330</span>
    </div>
    <div class="contact-row">
      <svg width="14" height="14" viewBox="0 0 24 24"><path fill="#fff" d="M6.6 10.8a15.1 15.1 0 0 0 6.6 6.6l2.2-2.2a1 1 0 0 1 1-.25 11.4 11.4 0 0 0 3.6.57 1 1 0 0 1 1 1V20a1 1 0 0 1-1 1A17 17 0 0 1 3 4a1 1 0 0 1 1-1h3.5a1 1 0 0 1 1 1c0 1.25.2 2.45.57 3.57a1 1 0 0 1-.25 1z"/></svg>
      <span>123 456 7890</span>
    </div>
    <div class="contact-row">
      <svg width="16" height="12" viewBox="0 0 16 12"><rect x="0.5" y="0.5" width="15" height="11" fill="none" stroke="#fff"/><path d="M0.5 0.5L8 7l7.5-6.5" fill="none" stroke="#fff"/></svg>
      <span>info@marlowvale.com</span>
    </div>
  </div>

  <div class="footer-col newsletter" style="left:812px">
    <h4>NEWSLETTER</h4>
    <p>Would you like to receive our exclusive news and update for sign up our newsletter?</p>
    <div class="email-field">Enter Email</div>
    <a class="btn" href="#">SUBSCRIBE</a>
  </div>

  <p class="copyright">Marlow Vale Stud, 2018 All Right Reserved</p>
</footer>

</div>
</body>
</html>
```